Animal Eye Clinic needs a Business card

We are a new veterinary ophthalmology practice (Ridgeline Pet Vision Care) and we need a business card designed. We only see animal eyes - we are not a regular veterinary clinic. We already have a logo. We are looking for a professional, good looking business card to hand out to our clients. We are looking for something simple but professional and contemporary. Our logo is likely the only picture/graphic that needs to be on the card.
Updates

Contact Information for Business Card

Delia Vossman, BSc, DVM, MSc, DipACVO
Veterinary Ophthalmologist

Phone: 250.418.3927
Email: ridgelinepetvisioncare@mailbox-example.net
Website: ridgelinepetvisioncare-example.net
Address: 1874 Thornbury Rd
Kelowna, BC, V1X 4M9

Colors

Designer to choose colors to be used in the design.

Requirements
Must have
• Our logo (attached)

```html
<!DOCTYPE html>
<html lang="en">
<head>
<meta charset="utf-8">
<title>Ridgeline Pet Vision Care – Business Card</title>
<link rel="stylesheet" href="https://fonts.googleapis.com/css2?family=Montserrat:ital,wght@0,600;0,700;1,700&family=Roboto:wght@300;400&display=swap">
<style>
  :root {
    --page: #d7d8d9;
    --card: #4a4b4d;
    --card-deep: #3f4042;
    --teal: #0f93a5;
    --teal-deep: #0a7f90;
    --white: #ffffff;
    --emboss: #555658;
  }
  * { box-sizing: border-box; margin: 0; padding: 0; }
  html, body { width: 1200px; height: 1125px; overflow: hidden; }
  body {
    background: var(--page);
    font-family: "Roboto", Arial, sans-serif;
    display: flex;
    flex-direction: column;
    align-items: center;
    justify-content: center;
    gap: 44px;
  }
  .card {
    position: relative;
    width: 860px;
    height: 491px;
    background: var(--card);
    border-bottom: 5px solid var(--teal);
    border-radius: 4px;
    overflow: hidden;
    box-shadow: 0 10px 24px rgba(0,0,0,.25);
  }

  /* Back side */
  .card-back .emboss-art {
    position: absolute;
    left: 70px;
    bottom: 0;
    width: 420px;
    height: 440px;
    border-radius: 50% 50% 0 0 / 40% 40% 0 0;
    background: linear-gradient(160deg, var(--emboss), var(--card-deep));
    box-shadow: inset 1px 1px 0 rgba(255,255,255,.08);
  }
  .card-back .back-name {
    position: absolute;
    right: 56px;
    top: 210px;
    font-family: "Montserrat", Arial, sans-serif;
    font-weight: 700;
    font-size: 30px;
    letter-spacing: 1px;
    text-transform: uppercase;
    color: var(--teal);
    text-align: right;
    line-height: 1.2;
  }

  /* Front side */
  .card-front .text-block { position: absolute; z-index: 2; }
  .brand {
    left: 48px;
    top: 40px;
    display: flex;
    align-items: center;
    gap: 14px;
  }
  .brand-dot {
    width: 44px;
    height: 44px;
    border-radius: 50%;
    background: var(--teal);
  }
  .brand-name {
    font-family: "Montserrat", Arial, sans-serif;
    font-weight: 700;
    font-size: 24px;
    text-transform: uppercase;
    color: var(--teal);
    letter-spacing: .5px;
  }
  .person {
    left: 48px;
    top: 118px;
  }
  .person-name {
    display: flex;
    align-items: center;
    gap: 14px;
    font-family: "Montserrat", Arial, sans-serif;
    font-style: italic;
    font-weight: 700;
    font-size: 26px;
    letter-spacing: 3px;
    text-transform: uppercase;
    color: var(--teal);
  }
  .person-name svg { width: 22px; height: 22px; }
  .credentials, .role {
    margin-left: 36px;
    font-size: 20px;
    line-height: 1.3;
    font-weight: 400;
  }
  .credentials { color: var(--teal); }
  .role { color: var(--white); }
  .address {
    left: 84px;
    top: 258px;
    color: var(--white);
    font-size: 20px;
    line-height: 1.3;
    font-weight: 300;
    font-style: normal;
  }
  .contacts {
    left: 48px;
    top: 340px;
    list-style: none;
    color: var(--white);
    font-size: 18px;
    line-height: 1.55;
    font-weight: 300;
  }
  .contacts li { display: flex; align-items: center; gap: 10px; white-space: nowrap; }
  .contacts svg { width: 17px; height: 17px; flex: none; }
  .front-art {
    position: absolute;
    z-index: 1;
    right: 0;
    bottom: 0;
    width: 370px;
    height: 420px;
    border-radius: 55% 45% 0 0 / 50% 50% 0 0;
    background: linear-gradient(150deg, var(--teal), var(--teal-deep));
  }
</style>
</head>
<body>

  <section class="card card-back" aria-label="Business card back">
    <div class="emboss-art" role="img" aria-label="Embossed clinic logo artwork"></div>
    <p class="back-name">Ridgeline Pet<br>Vision Care</p>
  </section>

  <section class="card card-front" aria-label="Business card front">
    <div class="front-art" role="img" aria-label="Clinic logo artwork in teal"></div>

    <div class="text-block brand">
      <span class="brand-dot"></span>
      <span class="brand-name">Ridgeline Pet Vision Care</span>
    </div>

    <div class="text-block person">
      <h1 class="person-name">
        <svg viewBox="0 0 22 22" aria-hidden="true"><path d="M2 2 L20 11 L2 20 Z" fill="var(--teal)"/></svg>
        Delia Vossman
      </h1>
      <p class="credentials">BSc, DVM, MSc, DipACVO</p>
      <p class="role">Veterinary Ophthalmologist</p>
    </div>

    <address class="text-block address">
      1874 Thornbury Rd<br>
      Kelowna, BC, V1X 4M9
    </address>

    <ul class="text-block contacts">
      <li>
        <svg viewBox="0 0 24 24" aria-hidden="true"><path fill="var(--teal)" d="M6.6 10.8a15.1 15.1 0 0 0 6.6 6.6l2.2-2.2a1 1 0 0 1 1-.25 11.4 11.4 0 0 0 3.6.57 1 1 0 0 1 1 1V20a1 1 0 0 1-1 1A17 17 0 0 1 3 4a1 1 0 0 1 1-1h3.5a1 1 0 0 1 1 1c0 1.25.2 2.45.57 3.57a1 1 0 0 1-.25 1z"/></svg>
        250.418.3927
      </li>
      <li>
        <svg viewBox="0 0 24 24" aria-hidden="true"><path fill="var(--teal)" d="M2 5h20v14H2z"/><path d="M2 5l10 8 10-8" fill="none" stroke="var(--card)" stroke-width="2"/></svg>
        ridgelinepetvisioncare@mailbox-example.net
      </li>
      <li>
        <svg viewBox="0 0 24 24" aria-hidden="true"><circle cx="12" cy="12" r="10" fill="var(--teal)"/><path d="M2 12h20M12 2c3 3 3 17 0 20M12 2c-3 3-3 17 0 20" fill="none" stroke="var(--card)" stroke-width="1.5"/></svg>
        ridgelinepetvisioncare-example.net
      </li>
    </ul>
  </section>

</body>
</html>
```